Redesign of business card for Cedar Ridge Mechanical

We are looking for a new design for our business cards for Cedar Ridge Mechanical. We are a plumbing & HVAC construction company, operating on the West Coast of Canada and USA. Logo attached.
Industry/Entity Type
Construction - Plumbing & HVAC
Contact Information for Business Card
Name, address, phone numbers, email, website address
Look and feel
Each slider illustrates characteristics of the customer's brand and the style your logo design should communicate.

```html
<!DOCTYPE html>
<html lang="en">
<head>
<meta charset="utf-8">
<title>Cedar Ridge Mechanical – Business Card</title>
<link rel="stylesheet" href="https://fonts.googleapis.com/css2?family=Lato:wght@400;700&display=swap">
<style>
  :root {
    --canvas: #e4e4e4;
    --ink: #111111;
    --paper: #ffffff;
    --night: #141414;
    --night-mark: #2c2c2c;
    --swoosh: #9a9a9a;
    --light-text: #f2f2f2;
  }
  * { margin: 0; padding: 0; box-sizing: border-box; }
  html, body {
    width: 1200px; height: 913px; overflow: hidden;
    background: var(--canvas);
    font-family: "Lato", sans-serif;
  }
  .stage {
    width: 1200px; height: 913px;
    display: flex; align-items: center; justify-content: center; gap: 50px;
  }
  .card {
    position: relative;
    width: 540px; height: 310px;
    border-radius: 18px;
    overflow: hidden;
    box-shadow: 0 10px 24px rgba(0,0,0,0.22);
  }
  /* Back side */
  .card-back { background: var(--night); display: flex; align-items: center; justify-content: center; }
  .back-mark { display: flex; align-items: center; gap: 16px; color: var(--night-mark); }
  .back-mark .mark-square { width: 34px; height: 34px; background: var(--night-mark); }
  .back-mark .mark-name { font-weight: 700; font-size: 30px; letter-spacing: 1px; text-transform: uppercase; line-height: 1.1; }

  /* Front side */
  .card-front { background: var(--paper); color: var(--ink); }
  .front-shape { position: absolute; inset: 0; }
  .front-logo { position: absolute; left: 28px; top: 62px; display: flex; align-items: center; gap: 12px; }
  .front-logo .mark-square { width: 26px; height: 26px; background: var(--ink); }
  .front-logo .mark-name { font-weight: 700; font-size: 22px; letter-spacing: 0.5px; text-transform: uppercase; line-height: 1.15; }
  .holder { position: absolute; right: 32px; top: 30px; text-align: right; }
  .holder-name { font-weight: 700; font-size: 19px; letter-spacing: 0.5px; }
  .holder-role { font-size: 12px; margin-top: 2px; }
  .holder-bar { position: absolute; right: 0; top: 28px; width: 12px; height: 40px; background: var(--ink); }
  .address { position: absolute; right: 24px; top: 150px; text-align: right; color: var(--light-text); font-size: 13px; line-height: 1.5; }
  .contacts { position: absolute; left: 26px; top: 212px; list-style: none; color: var(--light-text); font-size: 14px; }
  .contacts li { display: flex; align-items: center; gap: 8px; height: 21px; }
  .contacts svg { width: 12px; height: 12px; fill: var(--light-text); }
</style>
</head>
<body>
<main class="stage">
  <section class="card card-back" aria-label="Card back">
    <div class="back-mark">
      <span class="mark-square"></span>
      <span class="mark-name">Cedar Ridge<br>Mechanical</span>
    </div>
  </section>

  <section class="card card-front" aria-label="Card front">
    <svg class="front-shape" viewBox="0 0 540 310" preserveAspectRatio="none" aria-hidden="true">
      <path d="M0,198 Q300,182 540,92 L540,104 Q300,190 0,204 Z" fill="#9a9a9a"/>
      <path d="M0,206 Q300,194 540,112 L540,310 L0,310 Z" fill="#000"/>
    </svg>
    <div class="front-logo">
      <span class="mark-square"></span>
      <span class="mark-name">Cedar Ridge<br>Mechanical</span>
    </div>
    <div class="holder">
      <div class="holder-name">DANIEL HALE</div>
      <div class="holder-role">Managing Director</div>
    </div>
    <span class="holder-bar"></span>
    <div class="address">Your address, City<br>State, Zip 1234</div>
    <ul class="contacts">
      <li><svg viewBox="0 0 24 24"><path d="M6.6 10.8a15 15 0 0 0 6.6 6.6l2.2-2.2a1 1 0 0 1 1-.25 11.4 11.4 0 0 0 3.6.57 1 1 0 0 1 1 1V20a1 1 0 0 1-1 1A17 17 0 0 1 3 4a1 1 0 0 1 1-1h3.5a1 1 0 0 1 1 1c0 1.25.2 2.45.57 3.6a1 1 0 0 1-.25 1z"/></svg>123 456 789</li>
      <li><svg viewBox="0 0 24 24"><path d="M7 1h10a2 2 0 0 1 2 2v18a2 2 0 0 1-2 2H7a2 2 0 0 1-2-2V3a2 2 0 0 1 2-2zm0 3v14h10V4zm5 15.5a1 1 0 1 0 0 2 1 1 0 0 0 0-2z"/></svg>123 456 789</li>
      <li><svg viewBox="0 0 24 24"><path d="M2 5h20v14H2zm2 2v.5l8 5 8-5V7zm0 2.8V17h16V9.8l-8 5z"/></svg>info@youremail.com</li>
      <li><svg viewBox="0 0 24 24"><path d="M12 2a10 10 0 1 0 0 20 10 10 0 0 0 0-20zm0 2c.9 0 2.3 2 2.8 5H9.2C9.7 6 11.1 4 12 4zM4.3 11h3.8a18 18 0 0 0 0 2H4.3a8 8 0 0 1 0-2zm5 0h5.4a16 16 0 0 1 0 2H9.3a16 16 0 0 1 0-2zm6.6 0h3.8a8 8 0 0 1 0 2h-3.8a18 18 0 0 0 0-2zM9.2 15h5.6c-.5 3-1.9 5-2.8 5s-2.3-2-2.8-5z"/></svg>www.yourwebsite.com</li>
    </ul>
  </section>
</main>
</body>
</html>
```